Digital One Pager for Consulting Practice

I would like the essence of the content in my ppt consolidated into a one-pager. The one-pager will mainly be sent via email as a pdf and intended to excite and invite new clients and establish the credibility of my boutique high-end consulting firm. Infographics and symbols would be a plus. The target client should view the firm as providing premeir service. The client is getting a thought partner.

Target Market(s)

Large Medical Device Manufacturer Executives, Early-Stage Medical Device Manufacturer Executives, Partners at VC Firms

Industry/Entity Type

Medical Equipment

Colors
0355a3
f37122

Requirements
Must have
• Please match the color scheme in ppt. Please use the existing logo. I am very open to better graphics on the process. My photo does not need to be on the digital flyer. Hyper link to the website and email is needed.
Nice to have
• Infographics

```html
<!DOCTYPE html>
<html lang="en">
<head>
<meta charset="utf-8">
<title>Halden Ventures – One Pager</title>
<link href="https://fonts.googleapis.com/css2?family=EB+Garamond:wght@500;700&family=Arimo:wght@400;700&display=swap" rel="stylesheet">
<style>
:root{
  --navy:#2d3a54;
  --navy-dark:#1f2940;
  --slate:#5b6478;
  --grey:#c9ccd3;
  --paper:#f3f3f5;
  --orange:#e6461f;
  --bg:#e4ddd6;
  --white:#ffffff;
}
*{box-sizing:border-box;margin:0;padding:0}
html,body{width:1200px;height:790px;overflow:hidden;background:var(--bg)}
body{font-family:"Arimo",Arial,sans-serif;color:var(--navy)}
.page{position:absolute;left:300px;top:10px;width:600px;height:770px;background:var(--paper);overflow:hidden;box-shadow:0 4px 14px rgba(0,0,0,.18)}
.abs{position:absolute}
.top-band{left:0;top:0;width:600px;height:260px;background:linear-gradient(180deg,var(--navy-dark) 0%,var(--slate) 55%,var(--grey) 85%,var(--paper) 100%)}
.bottom-band{left:0;top:700px;width:600px;height:70px;background:linear-gradient(0deg,var(--navy-dark) 0%,var(--slate) 60%,var(--paper) 100%)}
.brand{left:180px;top:16px;width:240px;height:44px;border:2px solid var(--white);border-radius:10px;background:var(--navy);display:flex;align-items:center;justify-content:center;gap:8px;white-space:nowrap}
.brand-dot{width:11px;height:11px;border-radius:50%;background:var(--white)}
.brand-name{font-family:"EB Garamond",serif;font-weight:700;font-size:18px;color:var(--white);letter-spacing:1px}
.headline{left:0;width:600px;top:68px;text-align:center;font-family:"EB Garamond",serif;font-weight:700;font-size:18px;color:var(--white);letter-spacing:.5px;white-space:nowrap}
.pill{font-family:"EB Garamond",serif;font-weight:700;font-size:12px;color:var(--orange);background:var(--paper);border:1.5px solid var(--orange);padding:3px 12px;border-radius:3px;text-transform:uppercase;letter-spacing:.5px;white-space:nowrap}
.diagram{left:200px;top:148px;width:200px;height:200px}
.diff{left:0;width:600px;top:348px;text-align:center;font-family:"EB Garamond",serif;font-weight:700;font-size:15px;color:var(--orange);letter-spacing:.5px}
.panel{background:linear-gradient(160deg,#e6e7ea,#b9bdc6);border:2px solid var(--navy);border-radius:14px;padding:30px 10px 10px;font-size:10px;line-height:1.3}
.panel-title{position:absolute;left:8px;top:-2px;right:8px;background:var(--navy);color:var(--white);font-family:"EB Garamond",serif;font-weight:700;font-size:12px;text-transform:uppercase;padding:4px 8px;border-radius:0 0 6px 6px;white-space:nowrap}
.panel ul{list-style:none}
.panel li{position:relative;padding-left:11px;margin-bottom:4px}
.panel li::before{content:"";position:absolute;left:0;top:4px;width:6px;height:6px;border-radius:50%;background:var(--orange)}
.sub{font-family:"EB Garamond",serif;font-weight:700;font-size:12px;line-height:1.1;color:var(--orange);margin:3px 0 3px}
.flow-frame{left:205px;top:566px;width:385px;height:46px;border:2.5px solid var(--navy);border-radius:16px}
.flow{left:222px;top:572px;display:flex;align-items:center}
.step{background:var(--navy);color:var(--white);font-size:9px;line-height:1.15;text-align:center;display:flex;align-items:center;justify-content:center;border-radius:10px 0 10px 0;width:74px;height:34px;border:1.5px solid var(--white);box-shadow:0 2px 3px rgba(0,0,0,.3)}
.link{height:7px;width:18px;background:var(--orange);border-radius:4px}
.lane{left:10px;width:580px;height:40px;border:2.5px solid var(--navy);border-radius:16px;background:var(--paper);display:flex;align-items:center;padding-left:20px;font-family:"EB Garamond",serif;font-weight:700;font-size:14px;color:var(--navy);white-space:nowrap}
.badge{background:var(--navy);border-radius:3px}
.badge.light{background:#9aa3b3}
.contact{display:flex;align-items:center;gap:8px;font-family:"EB Garamond",serif;font-size:12.5px;color:var(--navy);text-decoration:none;white-space:nowrap}
.contact.on-dark{color:var(--white)}
.icon-box{width:20px;height:20px;background:var(--navy);border-radius:4px;display:flex;align-items:center;justify-content:center}
</style>
</head>
<body>
<main class="page">
  <div class="abs top-band"></div>
  <div class="abs bottom-band"></div>

  <div class="abs brand"><span class="brand-dot"></span><span class="brand-name">HALDEN VENTURES</span></div>
  <h1 class="abs headline">HALDEN VENTURES VALUE</h1>
  <span class="abs pill" style="left:235px;top:100px">Efficient Process</span>
  <span class="abs pill" style="left:430px;top:100px">Valued Network</span>
  <span class="abs pill" style="left:40px;top:142px;transform:rotate(-8deg)">Extensive Experience</span>

  <svg class="abs diagram" viewBox="0 0 200 200" role="img" aria-label="Experience, network and process combine into leverage">
    <circle cx="100" cy="106" r="70" fill="none" stroke="var(--orange)" stroke-width="4"/>
    <g font-family="Arimo, sans-serif" font-size="6" fill="#fff" text-anchor="middle">
      <circle cx="55" cy="60" r="28" fill="var(--navy)" stroke="#fff" stroke-width="2"/>
      <circle cx="55" cy="54" r="9" fill="none" stroke="#fff" stroke-width="1.5"/>
      <text x="55" y="76">EXPERIENCE</text>
      <circle cx="140" cy="50" r="28" fill="var(--navy)" stroke="#fff" stroke-width="2"/>
      <g stroke="#fff" stroke-width="1.3" fill="none"><circle cx="140" cy="46" r="4"/><line x1="140" y1="42" x2="140" y2="34"/><line x1="144" y1="46" x2="152" y2="46"/><line x1="136" y1="46" x2="128" y2="46"/><line x1="140" y1="50" x2="140" y2="58"/></g>
      <text x="140" y="68">NETWORK</text>
      <circle cx="100" cy="116" r="34" fill="var(--navy-dark)" stroke="#fff" stroke-width="2"/>
      <g stroke="#fff" stroke-width="1.5" fill="none"><line x1="100" y1="96" x2="100" y2="124"/><line x1="84" y1="102" x2="116" y2="102"/><path d="M84 102 l-6 12 h12 z M116 102 l-6 12 h12 z"/><line x1="92" y1="124" x2="108" y2="124"/></g>
      <text x="100" y="138" font-size="7">LEVERAGE</text>
      <circle cx="115" cy="172" r="24" fill="var(--navy)" stroke="#fff" stroke-width="2"/>
      <circle cx="115" cy="166" r="8" fill="none" stroke="#fff" stroke-width="1.5" stroke-dasharray="3 2"/>
      <text x="115" y="186">PROCESS</text>
    </g>
  </svg>

  <div class="abs diff">DIFFERENTIATORS</div>

  <section class="abs panel" style="left:18px;top:295px;width:175px;height:300px">
    <div class="panel-title">Experience</div>
    <ul>
      <li>Over a decade @FDA (Former Deputy Division Director)</li>
      <li>Expertise: Cardiovascular, Ophthalmology, General Hospital, Infection Control, Dental, Anesthesia, Respiratory</li>
      <li>Vice President Regulatory Affairs / Quality Assurance @Corvane (Fortune 150 Company)</li>
      <li>Initiated reorganization of department</li>
      <li>Led major compliance effort</li>
      <li>Successful FDA inspection (no observations)</li>
    </ul>
  </section>

  <section class="abs panel" style="left:203px;top:370px;width:198px;height:188px;padding-top:26px;font-size:9.5px">
    <div class="panel-title">Experience to Provide</div>
    <div class="sub">Executive Application Review</div>
    <ul>
      <li>Examples include: Presubmission, IDE, 510(k), 513(g), PMA, Refuse to Accept, Hold letter</li>
      <li>Troubleshooting</li>
    </ul>
    <div class="sub">Strategic Advice &amp; Diligence to Investors</div>
    <ul>
      <li>Validate &amp; Verify Founder Milestones</li>
      <li>Diligence portfolio company Regulatory and Quality systems</li>
    </ul>
  </section>

  <section class="abs panel" style="left:410px;top:258px;width:175px;height:300px;padding-top:26px">
    <div class="panel-title">Services</div>
    <div class="sub">Regulatory Strategy</div>
    <ul><li>RAQA Organizational Structure</li><li>Regulatory Pathway</li></ul>
    <div class="sub">FDA Communications</div>
    <ul><li>Deficiency Response</li><li>Application Review</li></ul>
    <div class="sub">Interim Executive Training Leadership</div>
    <ul><li>Compliance Remediation</li><li>Accelerated Product Registration</li></ul>
    <div class="sub">Training</div>
    <ul><li>FDA Communication</li><li>MDR Reporting</li></ul>
  </section>

  <div class="abs flow-frame"></div>
  <div class="abs flow">
    <div class="step">Exploratory Call</div><div class="link"></div>
    <div class="step">Regulatory Landscape</div><div class="link"></div>
    <div class="step">Problem Statement</div><div class="link"></div>
    <div class="step">Review &amp; Align on Deliverables</div>
  </div>

  <div class="abs lane" style="top:620px">Efficient Process
    <svg width="60" height="20" viewBox="0 0 60 20" style="margin-left:20px" aria-hidden="true"><path d="M0 7h44V1l14 9-14 9v-6H0z" fill="var(--navy)"/></svg>
  </div>
  <div class="abs lane" style="top:666px">Valued Partner Network
    <svg width="60" height="20" viewBox="0 0 60 20" style="margin-left:20px" aria-hidden="true"><path d="M0 7h44V1l14 9-14 9v-6H0z" fill="var(--navy)"/></svg>
  </div>

  <div class="abs badge" style="left:300px;top:629px;width:70px;height:22px" role="img" aria-label="Partner badge"></div>
  <div class="abs badge light" style="left:395px;top:629px;width:60px;height:22px" role="img" aria-label="Partner badge"></div>
  <div class="abs badge" style="left:485px;top:627px;width:50px;height:26px" role="img" aria-label="Partner badge"></div>
  <div class="abs badge light" style="left:275px;top:676px;width:60px;height:20px" role="img" aria-label="Partner badge"></div>
  <div class="abs badge light" style="left:345px;top:680px;width:55px;height:12px" role="img" aria-label="Partner badge"></div>

  <a class="abs contact" style="left:412px;top:676px" href="mailto:info@haldenventures.com">
    <span class="icon-box"><svg width="12" height="9" viewBox="0 0 12 9"><rect x=".5" y=".5" width="11" height="8" fill="none" stroke="#fff"/><path d="M.5.5 6 5l5.5-4.5" fill="none" stroke="#fff"/></svg></span>info@haldenventures.com</a>
  <a class="abs contact" style="left:250px;top:712px" href="tel:2025550148">
    <span class="icon-box"><svg width="8" height="12" viewBox="0 0 8 12"><rect x=".5" y=".5" width="7" height="11" rx="1" fill="none" stroke="#fff"/><circle cx="4" cy="9.5" r=".8" fill="#fff"/></svg></span>202.555.0148</a>
  <a class="abs contact on-dark" style="left:30px;top:742px" href="https://www.haldenventures.com">
    <span class="icon-box" style="background:var(--white)"><svg width="12" height="12" viewBox="0 0 12 12"><circle cx="6" cy="6" r="5" fill="none" stroke="var(--navy)"/><path d="M1 6h10M6 1c-3 3-3 7 0 10M6 1c3 3 3 7 0 10" fill="none" stroke="var(--navy)"/></svg></span>www.haldenventures.com</a>
</main>
</body>
</html>
```